Vantiqo custom business card design

Need a authentic, innovative business card design for a new mobile app business. I am uploading a few screen images from our app for you to view. I would like app design theme to match business card design. I can also send logo images.

```html
<!DOCTYPE html>
<html lang="en">
<head>
<meta charset="UTF-8">
<title>Vantiqo Business Card</title>
<link href="https://fonts.googleapis.com/css2?family=Montserrat:ital,wght@0,500;0,700;0,800;1,500&display=swap" rel="stylesheet">
<style>
  :root {
    --backdrop: #e2e0db;
    --card-white: #ffffff;
    --ink: #050505;
    --purple: #552383;
    --purple-deep: #3a1a5c;
    --purple-light: #9470b6;
    --disc-grey: #ececec;
  }
  html, body {
    margin: 0;
    padding: 0;
    width: 1200px;
    height: 1200px;
    overflow: hidden;
    background: var(--backdrop);
  }
  .canvas {
    position: relative;
    width: 1200px;
    height: 1200px;
  }
  .card {
    position: absolute;
    left: 150px;
    width: 900px;
    height: 514px;
    background: var(--card-white);
    box-shadow: 0 6px 18px rgba(0,0,0,0.12);
    overflow: hidden;
  }
  .card--front { top: 70px; }
  .card--back  { top: 616px; }
  .card svg { display: block; width: 900px; height: 514px; }
  .brand-name {
    font-family: 'Montserrat', sans-serif;
    font-weight: 800;
  }
  .person-name {
    font-family: 'Montserrat', sans-serif;
    font-weight: 700;
    font-size: 40px;
    fill: var(--ink);
  }
  .tagline {
    font-family: 'Montserrat', sans-serif;
    font-style: italic;
    font-weight: 500;
    font-size: 17px;
    fill: var(--ink);
  }
  .contact-line {
    font-family: 'Montserrat', sans-serif;
    font-weight: 700;
    font-size: 22px;
    fill: var(--ink);
  }
</style>
</head>
<body>
<div class="canvas">

  <!-- Front face: brand mark -->
  <div class="card card--front">
    <svg viewBox="0 0 900 514" xmlns="http://www.w3.org/2000/svg">
      <rect class="card-base" width="900" height="514" fill="var(--card-white)"/>
      <polygon class="band-black" points="0,514 900,372 900,468 640,514" fill="var(--ink)"/>
      <polygon class="accent-right" points="640,514 900,468 900,514" fill="var(--purple)"/>
      <polygon class="accent-dark" points="0,345 270,470 0,430" fill="var(--purple)"/>
      <polygon class="accent-light" points="0,430 270,470 0,500" fill="var(--purple-light)"/>
      <polygon class="accent-black" points="0,500 270,470 0,514" fill="var(--ink)"/>
      <circle class="brand-dot" cx="450" cy="170" r="72" fill="var(--purple)"/>
      <text class="brand-name" x="450" y="318" text-anchor="middle" font-size="64" fill="var(--ink)">Vantiqo</text>
    </svg>
  </div>

  <!-- Back face: contact details -->
  <div class="card card--back">
    <svg viewBox="0 0 900 514" xmlns="http://www.w3.org/2000/svg">
      <defs>
        <linearGradient id="purpleFade" x1="0" y1="0" x2="0" y2="1">
          <stop offset="0" stop-color="var(--purple-deep)"/>
          <stop offset="1" stop-color="var(--purple)"/>
        </linearGradient>
      </defs>
      <rect class="card-base" width="900" height="514" fill="var(--card-white)"/>
      <polygon class="panel-black" points="0,0 425,0 190,430 0,448" fill="var(--ink)"/>
      <polygon class="stripe-dark" points="40,0 150,0 0,30" fill="var(--purple)"/>
      <polygon class="stripe-light" points="150,0 215,0 0,52 0,30" fill="var(--purple-light)"/>
      <line class="divider-white" x1="0" y1="458" x2="150" y2="434" stroke="var(--card-white)" stroke-width="5"/>
      <polygon class="panel-purple" points="0,468 190,440 355,395 440,514 0,514" fill="url(#purpleFade)"/>
      <rect class="edge-strip" x="862" y="0" width="38" height="514" fill="var(--ink)"/>

      <circle class="badge-ring" cx="235" cy="320" r="132" fill="var(--card-white)"/>
      <circle class="badge-fill" cx="235" cy="320" r="112" fill="var(--disc-grey)"/>

      <text class="brand-name" x="165" y="140" text-anchor="middle" font-size="46" fill="var(--card-white)">Vantiqo</text>

      <text class="person-name" x="815" y="118" text-anchor="end">Your Name</text>
      <line class="name-rule" x1="430" y1="130" x2="830" y2="130" stroke="var(--ink)" stroke-width="2"/>
      <text class="tagline" x="815" y="155" text-anchor="end">Your Tagline or Position here</text>

      <g class="contact-list">
        <text class="contact-line" x="752" y="248" text-anchor="end">+000 12345 875</text>
        <text class="contact-line" x="752" y="294" text-anchor="end">urwebiste.com</text>
        <text class="contact-line" x="752" y="340" text-anchor="end">ur@mailhub.com</text>
        <text class="contact-line" x="752" y="386" text-anchor="end">Street Address, 01 USA</text>
      </g>

      <g class="contact-icons" fill="var(--purple)">
        <!-- phone -->
        <rect x="768" y="222" width="34" height="34" rx="5"/>
        <rect x="777" y="228" width="16" height="22" rx="2" fill="none" stroke="var(--card-white)" stroke-width="2.5"/>
        <!-- globe -->
        <rect x="768" y="268" width="34" height="34" rx="5"/>
        <g fill="none" stroke="var(--card-white)" stroke-width="2">
          <circle cx="785" cy="285" r="11"/>
          <ellipse cx="785" cy="285" rx="5" ry="11"/>
          <line x1="774" y1="285" x2="796" y2="285"/>
          <line x1="776" y1="279" x2="794" y2="279"/>
          <line x1="776" y1="291" x2="794" y2="291"/>
        </g>
        <!-- mail -->
        <rect x="768" y="314" width="34" height="34" rx="5"/>
        <g fill="none" stroke="var(--card-white)" stroke-width="2.5">
          <rect x="775" y="322" width="20" height="15"/>
          <polyline points="775,322 785,331 795,322"/>
        </g>
        <!-- pin -->
        <rect x="768" y="360" width="34" height="34" rx="5"/>
        <path d="M785 387 C777 378 776 374 776 371 A9 9 0 0 1 794 371 C794 374 793 378 785 387 Z" fill="var(--card-white)"/>
        <circle cx="785" cy="371" r="3.5" fill="var(--purple)"/>
      </g>
    </svg>
  </div>

</div>
</body>
</html>
```